Bright and beautiful business card for a coach

I'm a personal and business coach based in Perth, Australia. I need a business card that whilst subtle and elegant, will stand out and appeal on a table full of cards.

My business name is Fern Mentoring and the business card must represent the warmth and brightness implied in the name, without being gimmicky. It must have a warmth and appeal and be easy to read.

I prefer clean, minimalist designs.

It must align with the feel of my website and socials: https://www.fernmentoring-example.com.au/
https://www.instagram.com/fernmentoringau/
https://www.facebook.com/fernmentoringau
Updates

Hi Designers Thank you so much for taking the time to submit designs. I wonder if I could have explained myself a little better. Most of the designs that have been submitted look rather formal and many have quite corporate looking embellishments on them (to my eye). I would like softer, warmer, more organic. I’m open to people playing about and being more abstract, using softer embellishments (e.g the line drawing flowers and grasses I’ve used in my socials) incorporating other colours from my palette or like the social icons in my email signature (in PDF), perhaps playing with size/oversize, playing with the bleed. Please don’t be constrained by what I’ve already done, it merely needs to compliment. I’m sorry if I’m not using the right words or have led you astray. I’m no designer, but I’ve done my website, socials, email signature etc all myself (my logo was a design contest) and I was really hoping for my business card to be something more creative than I could have made with a template. Reminder: No black cards/sides please. Thank you 😊

Target Market(s)

Individuals, most likely but not all female. Creative thinkers. Likely professionals.

Industry/Entity Type

Business & Personal Coach

Contact Information for Business Card

(Fern Mentoring Logo) Name: Greta Pellham; Title: Business & Personal Coach; Phone number: +61 (0)458 913307; Email: greta@fernmentoring-example.com.au; Website: https://fernmentoring-example.com.au; Social icons for Facebook, Instagram & LinkedIn: @fernmentoringAU. Optional strapline: "A thinking partner to help you cut through the noise"

Font styles to use
Sans Serif

Colors
00AB8E
00BBA5
67D7C9
C6EFE9
E9F9F6
59FF00
82FF00
B8FF75
E3FFCB
F4FFEA
FFC000
F8CF3A
FAE287
FDF2CF
FEFAEE

Requirements
Must have
• Must align with feel of my website and socials. Must have a pop of #FFC000 (possibly whole of one side, or at least a block). Bright or white background. Easy to read.
Nice to have
• Possibly incorporate the sunshine/grass picture I have used in website and socials - will upload.
Should not have
• Must not be black or dark. Not impersonal or corporate looking.

```html
<!DOCTYPE html>
<html lang="en">
<head>
<meta charset="utf-8">
<title>Fern Mentoring – Business Card</title>
<link rel="stylesheet" href="https://fonts.googleapis.com/css2?family=Poppins:wght@400;500&family=Sacramento&display=swap">
<style>
  :root {
    --backdrop: #dadddd;
    --card-white: #ffffff;
    --gold-deep: #c27b25;
    --gold-bright: #fbbf14;
    --gold-text: #c98a22;
    --grey-text: #6f6f73;
    --white: #ffffff;
    --grass-dark: #2f5a17;
    --grass-mid: #5e8f2c;
    --grass-light: #9cbc4f;
    --sun-glow: #fbe3bd;
  }
  * { box-sizing: border-box; margin: 0; padding: 0; }
  html, body {
    width: 1200px; height: 928px; overflow: hidden;
    background: var(--backdrop);
    font-family: "Poppins", sans-serif;
  }
  .canvas { position: relative; width: 1200px; height: 928px; }

  .card {
    position: absolute;
    border-radius: 16px;
    overflow: hidden;
  }

  /* Front side */
  .card-front { left: 267px; top: 59px; width: 670px; height: 382px; }
  .front-photo {
    position: absolute; inset: 0;
    background:
      radial-gradient(circle at 70% 8%, var(--sun-glow) 0%, rgba(245,200,140,.6) 14%, rgba(150,170,80,0) 40%),
      linear-gradient(180deg, var(--grass-mid) 0%, var(--grass-light) 45%, var(--grass-mid) 75%, var(--grass-dark) 100%);
  }
  .front-brand {
    position: absolute; left: 0; right: 0; top: 168px;
    text-align: center;
    color: var(--white);
    font-size: 40px; font-weight: 500; letter-spacing: 2px;
    white-space: nowrap;
  }
  .front-social {
    position: absolute; left: 0; right: 0; top: 324px;
    display: flex; justify-content: center; align-items: center; gap: 8px;
    color: var(--white); font-size: 15px; font-weight: 400;
    white-space: nowrap;
  }
  .front-social .dot {
    width: 20px; height: 20px; border-radius: 50%; background: var(--white);
  }

  /* Back side */
  .card-back {
    left: 264px; top: 484px; width: 676px; height: 386px;
    background: var(--card-white);
  }
  .back-brand {
    position: absolute; left: 48px; top: 160px;
    display: flex; align-items: center; gap: 12px;
    color: var(--gold-text); font-size: 30px; font-weight: 500;
    white-space: nowrap;
  }
  .back-brand .dot {
    width: 22px; height: 22px; border-radius: 50%; background: var(--gold-bright);
  }
  .person-name {
    position: absolute; left: 370px; top: 90px;
    font-family: "Sacramento", cursive;
    font-size: 48px; line-height: 1;
    color: var(--gold-text);
    white-space: nowrap;
  }
  .person-title {
    position: absolute; left: 374px; top: 160px;
    font-size: 15.5px; color: var(--grey-text);
    white-space: nowrap;
  }
  .contact-list {
    position: absolute; left: 374px; top: 220px;
    list-style: none;
  }
  .contact-list li {
    display: flex; align-items: center; gap: 7px;
    height: 24px;
    font-size: 14px; color: var(--grey-text);
    white-space: nowrap;
  }
  .contact-list svg { width: 15px; height: 15px; flex: none; }
  .strapline {
    position: absolute; left: 0; right: 0; top: 324px; height: 32px;
    background: linear-gradient(90deg, var(--gold-deep), var(--gold-bright));
    color: var(--white);
    font-size: 17.5px; font-weight: 500; letter-spacing: .5px;
    display: flex; align-items: center; justify-content: center;
    white-space: nowrap;
  }
</style>
</head>
<body>
<main class="canvas">

  <section class="card card-front">
    <div class="front-photo" role="img" aria-label="Sunlit meadow of green grass with a warm sun glow in the upper right"></div>
    <div class="front-brand">Fern Mentoring</div>
    <div class="front-social"><span class="dot"></span><span>@fernmentoringAU</span></div>
  </section>

  <section class="card card-back">
    <div class="back-brand"><span class="dot"></span><span>Fern Mentoring</span></div>

    <div class="person-name">Greta Pellham</div>
    <div class="person-title">Business &amp; Personal Coach</div>

    <ul class="contact-list">
      <li>
        <svg viewBox="0 0 16 16" aria-hidden="true"><circle cx="8" cy="8" r="8" fill="#d9921d"/><path d="M5.2 4.2l1.4-.2.8 2-1 .8a6 6 0 0 0 2.8 2.8l.8-1 2 .8-.2 1.4c-.2.6-.8.9-1.4.8A7 7 0 0 1 4.4 5.6c-.1-.6.2-1.2.8-1.4z" fill="#fff"/></svg>
        <span>+61 (0)458 913307</span>
      </li>
      <li>
        <svg viewBox="0 0 16 16" aria-hidden="true"><circle cx="8" cy="8" r="8" fill="#d9921d"/><rect x="4" y="5.2" width="8" height="5.6" rx=".6" fill="#fff"/><path d="M4.3 5.6L8 8.4l3.7-2.8" stroke="#d9921d" stroke-width=".9" fill="none"/></svg>
        <span>greta@fernmentoring-example.com.au</span>
      </li>
      <li>
        <svg viewBox="0 0 16 16" aria-hidden="true"><circle cx="8" cy="8" r="8" fill="#d9921d"/><circle cx="8" cy="8" r="4" fill="none" stroke="#fff" stroke-width="1.1"/><path d="M4 8h8M8 4c-1.6 2.4-1.6 5.6 0 8M8 4c1.6 2.4 1.6 5.6 0 8" stroke="#fff" stroke-width=".9" fill="none"/></svg>
        <span>www.fernmentoring-example.com.au</span>
      </li>
    </ul>

    <div class="strapline">A thinking partner to help you cut through the noise</div>
  </section>

</main>
</body>
</html>
```